Accounting firm needing business card / letterhead designed
Marcus L. Trenholm, CPA
marcus@veltrowledger.com
www.veltrowledger.com
842 E Alder Ave Larkfield, NY 43827
555-562-0974

```html
<!DOCTYPE html>
<html lang="en">
<head>
<meta charset="utf-8">
<title>Veltro Ledger — Business Card</title>
<link rel="stylesheet" href="https://fonts.googleapis.com/css2?family=Michroma&family=Roboto:wght@400&display=swap">
<style>
  :root {
    --backdrop: #d4d4d4;
    --card-white: #f7f7f7;
    --navy: #252062;
    --ink-grey: #555555;
    --white: #ffffff;
  }
  html, body {
    margin: 0;
    padding: 0;
    width: 1200px;
    height: 960px;
    overflow: hidden;
    background: var(--backdrop);
  }
  .canvas {
    position: relative;
    width: 1200px;
    height: 960px;
  }
  .card {
    position: absolute;
    left: 320px;
    width: 600px;
    border-radius: 20px;
    box-sizing: border-box;
  }
  .card-front {
    top: 98px;
    height: 350px;
    background: var(--card-white);
  }
  .brand-name {
    position: absolute;
    left: 0;
    right: 0;
    top: 145px;
    margin: 0;
    text-align: center;
    font-family: "Michroma", sans-serif;
    font-size: 42px;
    line-height: 1;
    letter-spacing: 0.02em;
    color: var(--navy);
    font-weight: 400;
  }
  .front-web {
    position: absolute;
    left: 0;
    right: 0;
    top: 291px;
    margin: 0;
    text-align: center;
    font-family: "Roboto", sans-serif;
    font-size: 14px;
    letter-spacing: 0.55em;
    color: var(--ink-grey);
  }
  .card-back {
    top: 493px;
    height: 342px;
    background: var(--navy);
  }
  .holder-name {
    position: absolute;
    left: 32px;
    top: 32px;
    margin: 0;
    font-family: "Michroma", sans-serif;
    font-size: 15px;
    font-weight: 400;
    letter-spacing: 0.02em;
    color: var(--white);
    text-transform: uppercase;
  }
  .name-rule {
    position: absolute;
    left: 30px;
    top: 62px;
    width: 535px;
    height: 2px;
    background: linear-gradient(to right, rgba(255,255,255,0.95), rgba(255,255,255,0.55) 70%, rgba(255,255,255,0));
  }
  .contact {
    position: absolute;
    right: 35px;
    bottom: 28px;
    margin: 0;
    text-align: right;
    font-family: "Roboto", sans-serif;
    font-style: normal;
    font-size: 14px;
    line-height: 21px;
    color: var(--white);
  }
</style>
</head>
<body>
<main class="canvas">
  <section class="card card-front">
    <h1 class="brand-name">VELTRO LEDGER</h1>
    <p class="front-web">www.veltrowledger.com</p>
  </section>
  <section class="card card-back">
    <h2 class="holder-name">Marcus L. Trenholm, CPA</h2>
    <div class="name-rule"></div>
    <address class="contact">
      842 E Alder Ave, Larkfield, NY 43827<br>
      C: 555-562-0974 E: marcus@veltrowledger.com W: www.veltrowledger.com
    </address>
  </section>
</main>
</body>
</html>
```